Executive recruiting firm in need of business card design

Executive recruiting firm looking for a sleek, classy and modern business card design; card itself will be square shape, rounded edges and soft touch paper, our colors are dark blues in the navy color scale, silvers and grays. Reference our website for a better idea of our company's feel and goals at Tarvex-Up.com - our company message is "Employee Engagement Begins at Recruitment" this should be on the card

```html
<!DOCTYPE html>
<html lang="en">
<head>
<meta charset="utf-8">
<title>Tarvex-Up Business Card</title>
<link href="https://fonts.googleapis.com/css2?family=Jost:wght@300&family=Barlow:wght@400;600;700&display=swap" rel="stylesheet">
<style>
  :root {
    --backdrop: #e6e6e6;
    --navy: #141848;
    --navy-deep: #10133c;
    --navy-soft: #1c2156;
    --card-white: #fbfbfb;
    --text-gray: #737373;
    --white: #ffffff;
  }
  * { margin: 0; padding: 0; box-sizing: border-box; }
  html, body {
    width: 1200px; height: 624px; overflow: hidden;
    background: var(--backdrop);
  }
  .stage { position: relative; width: 1200px; height: 624px; }
  .card {
    position: absolute; top: 152px;
    width: 320px; height: 320px;
    border-radius: 16px; overflow: hidden;
  }
  .card--front { left: 218px; background: var(--navy); }
  .card--back { left: 662px; background: var(--card-white); }

  .front-photo {
    position: absolute; inset: 0;
    background: linear-gradient(180deg, var(--navy-deep) 0%, var(--navy) 55%, var(--navy-soft) 100%);
  }

  .brand {
    position: absolute; left: 0; right: 0;
    text-align: center; white-space: nowrap;
  }
  .brand__name {
    font-family: "Jost", sans-serif; font-weight: 300;
    font-size: 42px; letter-spacing: 4px; line-height: 1;
  }
  .brand__tagline {
    font-family: "Jost", sans-serif; font-weight: 300;
    font-size: 8px; letter-spacing: 1.2px; margin-top: 6px;
  }
  .card--front .brand { top: 136px; color: var(--white); }
  .card--back .brand { top: 48px; color: var(--navy); }

  .person {
    position: absolute; left: 21px; top: 164px;
    font-family: "Barlow", sans-serif;
  }
  .person__name { font-size: 19px; font-weight: 700; color: var(--navy); line-height: 1.1; }
  .person__role { font-size: 12.5px; font-weight: 400; color: var(--text-gray); margin-top: 3px; }

  .contacts {
    position: absolute; left: 21px; top: 228px;
    list-style: none;
    font-family: "Barlow", sans-serif; font-size: 13px; color: var(--text-gray);
  }
  .contacts li { display: flex; align-items: center; height: 18px; }
  .contacts svg { width: 12px; height: 12px; margin-right: 11px; fill: var(--navy); flex: none; }
  .contacts .site-name { color: var(--navy); font-weight: 600; }
</style>
</head>
<body>
<main class="stage">
  <section class="card card--front">
    <div class="front-photo" role="img" aria-label="Dark navy-toned photo of a professional standing at an office window"></div>
    <div class="brand">
      <p class="brand__name">TARVEX UP</p>
      <p class="brand__tagline">Employee Engagement Begins at Recruitment</p>
    </div>
  </section>

  <section class="card card--back">
    <div class="brand">
      <p class="brand__name">TARVEX UP</p>
      <p class="brand__tagline">Employee Engagement Begins at Recruitment</p>
    </div>

    <div class="person">
      <p class="person__name">Employee Name</p>
      <p class="person__role">Managing Director</p>
    </div>

    <ul class="contacts">
      <li>
        <svg viewBox="0 0 12 12" aria-hidden="true"><path d="M1 4.5C1 3 3 2 6 2s5 1 5 2.5V5H8.5V4H3.5v1H1z"/><path d="M3 5.5h6l1.5 4.5h-9z"/></svg>
        00-1234-1234-55
      </li>
      <li>
        <svg viewBox="0 0 12 12" aria-hidden="true"><path d="M1 2.5h10v7H1z M2 3.5l4 3 4-3" stroke="#fbfbfb" stroke-width="0.8"/></svg>
        employee@tarvex-up.com
      </li>
      <li>
        <svg viewBox="0 0 12 12" aria-hidden="true"><circle cx="6" cy="6" r="5"/><path d="M1 6h10M6 1v10M2 3.5h8M2 8.5h8" stroke="#fbfbfb" stroke-width="0.7" fill="none"/><ellipse cx="6" cy="6" rx="2.2" ry="5" stroke="#fbfbfb" stroke-width="0.7" fill="none"/></svg>
        www.<span class="site-name">tarvex-up</span>.com
      </li>
      <li>482 W Larkin Ave, Marlow Bay, CA</li>
    </ul>
  </section>
</main>
</body>
</html>
```